Business Cards for a law firm

Business cards for our law firm. Use our silhoette logo and OAK PARTNERS - check our website (www.oakpartners.example)

Contact Information for Business Card

our silhouette logo, OAK PARTNERS, 800-555-0147, Dorian Pemberton, dorian@oakpartners.example

Requirements
Must have
• our silhouette logo, OAK PARTNERS, 800-555-0147, Dorian Pemberton, dorian@oakpartners.example

```html
<!DOCTYPE html>
<html lang="en">
<head>
<meta charset="utf-8">
<title>Oak Partners – Business Cards</title>
<link href="https://fonts.googleapis.com/css2?family=Montserrat:wght@300;400;600&display=swap" rel="stylesheet">
<style>
  :root {
    --stage: #3b3b3c;
    --navy: #23346b;
    --navy-soft: #3c4f96;
    --paper: #ffffff;
    --ink-grey: #6b6b6b;
  }
  html, body {
    margin: 0;
    width: 1200px;
    height: 689px;
    overflow: hidden;
    background: var(--stage);
    font-family: "Montserrat", sans-serif;
  }
  .stage {
    position: relative;
    width: 1200px;
    height: 689px;
  }
  .card {
    position: absolute;
    top: 200px;
    width: 500px;
    height: 286px;
    box-sizing: border-box;
  }
  /* back side */
  .card-back {
    left: 60px;
    background: var(--navy);
    display: flex;
    align-items: center;
    justify-content: center;
  }
  .back-mark {
    display: flex;
    align-items: center;
    gap: 10px;
    color: var(--navy-soft);
    font-weight: 600;
    font-size: 20px;
    letter-spacing: 3px;
  }
  .back-mark .mark-square {
    width: 16px;
    height: 16px;
    background: var(--navy-soft);
  }
  /* front side */
  .card-front {
    left: 640px;
    background: var(--paper);
  }
  .brand {
    position: absolute;
    left: 36px;
    top: 40px;
    display: flex;
    align-items: center;
    gap: 10px;
    color: var(--navy);
    font-weight: 600;
    font-size: 19px;
    letter-spacing: 3px;
  }
  .brand .mark-square {
    width: 14px;
    height: 14px;
    background: var(--navy);
  }
  .holder-name {
    position: absolute;
    right: 30px;
    top: 122px;
    color: var(--navy);
    font-weight: 600;
    font-size: 17px;
    letter-spacing: 1.5px;
    text-transform: uppercase;
  }
  .divider {
    position: absolute;
    left: 150px;
    right: 28px;
    top: 152px;
    height: 1px;
    background: var(--navy);
  }
  .contact-list {
    position: absolute;
    left: 150px;
    top: 174px;
    margin: 0;
    padding: 0;
    list-style: none;
    color: var(--ink-grey);
    font-weight: 300;
    font-size: 13px;
    line-height: 22px;
  }
  .contact-list li {
    display: flex;
    align-items: center;
    gap: 10px;
  }
  .contact-list svg {
    width: 11px;
    height: 11px;
    fill: var(--navy);
  }
</style>
</head>
<body>
<main class="stage">
  <section class="card card-back" aria-label="Card back">
    <div class="back-mark">
      <span class="mark-square"></span>
      <span>OAK PARTNERS</span>
    </div>
  </section>

  <section class="card card-front" aria-label="Card front">
    <div class="brand">
      <span class="mark-square"></span>
      <span>OAK PARTNERS</span>
    </div>
    <div class="holder-name">Dorian Pemberton</div>
    <div class="divider"></div>
    <ul class="contact-list">
      <li>
        <svg viewBox="0 0 12 12" aria-hidden="true"><path d="M2.5 0.8 4.3 2.8 3.4 4.2C4 5.7 6.3 8 7.8 8.6L9.2 7.7 11.2 9.5 10 11.2C5.8 11 1 6.2 0.8 2Z"/></svg>
        <span>800-555-0147</span>
      </li>
      <li>
        <svg viewBox="0 0 12 12" aria-hidden="true"><path d="M0.5 2.5h11v7h-11z M0.5 2.5 6 6.8 11.5 2.5" stroke="#fff" stroke-width="0.8"/></svg>
        <span>dorian@oakpartners.example</span>
      </li>
      <li>
        <svg viewBox="0 0 12 12" aria-hidden="true"><circle cx="6" cy="6" r="5.5"/><path d="M0.5 6h11M6 0.5c2.5 3 2.5 8 0 11M6 0.5c-2.5 3-2.5 8 0 11" stroke="#fff" stroke-width="0.7" fill="none"/></svg>
        <span>www.oakpartners.example</span>
      </li>
    </ul>
  </section>
</main>
</body>
</html>
```